Every Shelf Set Neatly or ESN Organized needs a business card design. ESN Organized is a professi

We need a business card design that is clean, sharp and conveys a sense of organization. I already have a logo.

Target Market(s)

Families (specifically mothers), small business owners, parents, seniors

Industry/Entity Type

Business

Contact Information for Business Card

My website is www.esnorganized-example.com and my Facebook page is http://www.sociallink-example.com/everyshelfsetneatly. The phone number is 418-552-7094 and I want to be listed as Lorna M. Pelham, Owner

Requirements
Must have
• My logo.

```html
<!DOCTYPE html>
<html lang="en">
<head>
<meta charset="utf-8">
<title>ESN Organized — Business Card</title>
<link rel="stylesheet" href="https://fonts.googleapis.com/css2?family=Montserrat:wght@400;500&family=Questrial&display=swap">
<style>
  :root {
    --backdrop: #e9e6e1;
    --card: #f7f7f6;
    --card-edge: #d9d9d6;
    --brand-blue: #2f5fa8;
    --ink: #1c1c1c;
    --bar-dark: #1e1f22;
    --social-square: #3d5a8f;
  }
  * { margin: 0; padding: 0; box-sizing: border-box; }
  html, body {
    width: 1200px;
    height: 969px;
    overflow: hidden;
    background: var(--backdrop);
  }
  .canvas {
    position: relative;
    width: 1200px;
    height: 969px;
  }
  .business-card {
    position: absolute;
    left: 100px;
    top: 200px;
    width: 1000px;
    height: 569px;
    background: var(--card);
    border: 1px solid var(--card-edge);
    box-shadow: 0 18px 40px rgba(0, 0, 0, 0.12);
    overflow: hidden;
  }
  .social-square {
    position: absolute;
    top: 22px;
    right: 26px;
    width: 38px;
    height: 38px;
    border-radius: 4px;
    background: var(--social-square);
  }
  .brand-name {
    position: absolute;
    left: 0;
    right: 0;
    top: 160px;
    text-align: center;
    font-family: "Montserrat", sans-serif;
    font-weight: 500;
    font-size: 72px;
    letter-spacing: 6px;
    color: var(--brand-blue);
  }
  .owner {
    position: absolute;
    left: 66px;
    top: 420px;
    font-family: "Questrial", sans-serif;
  }
  .owner-name {
    font-size: 36px;
    color: var(--brand-blue);
    letter-spacing: 1px;
  }
  .owner-title {
    margin-top: 4px;
    font-size: 27px;
    color: var(--ink);
  }
  .contact {
    position: absolute;
    right: 44px;
    top: 428px;
    text-align: right;
    font-family: "Questrial", sans-serif;
    font-size: 28px;
    line-height: 40px;
    color: var(--ink);
  }
  .contact-label { color: var(--brand-blue); }
  .footer-bar {
    position: absolute;
    left: 0;
    bottom: 0;
    width: 1000px;
    height: 16px;
  }
</style>
</head>
<body>
<main class="canvas">
  <section class="business-card">
    <span class="social-square" aria-label="Social page"></span>

    <h1 class="brand-name">ESN Organized</h1>

    <div class="owner">
      <p class="owner-name">Lorna M. Pelham</p>
      <p class="owner-title">Owner</p>
    </div>

    <div class="contact">
      <p><span class="contact-label">P</span> : 418-552-7094</p>
      <p>esnorganized-example.com</p>
    </div>

    <svg class="footer-bar" viewBox="0 0 1000 16" preserveAspectRatio="none" aria-hidden="true">
      <polygon points="178,0 290,0 280,16 178,16" fill="var(--brand-blue)"/>
      <polygon points="292,0 1000,0 1000,16 282,16" fill="var(--bar-dark)"/>
    </svg>
  </section>
</main>
</body>
</html>
```